Business Card Design

New business card design

Target Market(s)

Residential & Commercial Property Managers

Industry/Entity Type

Plumbing Services

Contact Information for Business Card

Name - Rowan Keddle, title - Director, Phone Number - 0431 286 517, email - rowan@tbk-plumbing.com.au, Company ABN - 73 215 904 386,

Font styles to use
Sans Serif

Colors
0054AA
0677BA
7BADD7
CADEEF
E8F1F8

```html
<!DOCTYPE html>
<html lang="en">
<head>
<meta charset="utf-8">
<title>TBK Plumbing Services – Business Card</title>
<link rel="stylesheet" href="https://fonts.googleapis.com/css2?family=Poppins:wght@300;400;500&display=swap">
<style>
  :root{
    --bg:#1f1f1f;
    --paper:#ffffff;
    --ink:#1b222b;
    --sky:#23a9e1;
    --sky-deep:#1b95cc;
    --taupe:#716759;
    --taupe-text:#8b8174;
    --white:#ffffff;
  }
  *{margin:0;padding:0;box-sizing:border-box}
  html,body{width:1200px;height:780px;overflow:hidden;background:var(--bg);font-family:'Poppins',sans-serif}
  .stage{position:relative;width:1200px;height:780px}
  .card{position:absolute;top:225px;width:540px;height:330px;overflow:hidden;box-shadow:0 14px 30px rgba(0,0,0,.45)}
  .card--front{left:40px;background:var(--paper)}
  .card--back{left:620px;background:var(--sky)}

  .wordmark{position:absolute;text-align:center}
  .wordmark__name{display:block;font-weight:300;line-height:1;letter-spacing:4px}
  .wordmark__tag{display:block;font-weight:400;text-transform:lowercase;letter-spacing:9px}
  .card--front .wordmark{left:250px;top:40px;width:250px}
  .card--front .wordmark__name{font-size:104px;color:var(--ink)}
  .card--front .wordmark__tag{font-size:10px;color:var(--taupe-text);margin-top:4px}
  .card--back .wordmark{right:38px;bottom:42px;width:170px}
  .card--back .wordmark__name{font-size:68px;color:var(--white)}
  .card--back .wordmark__tag{font-size:7px;color:var(--white);letter-spacing:6px;margin-top:2px}

  .name-band{position:absolute;left:0;top:172px;width:262px;height:56px;background:var(--ink);padding:4px 26px 0 0;text-align:right}
  .name-band__name{font-size:25px;font-weight:400;color:var(--sky);line-height:1.15}
  .name-band__title{font-size:11px;color:var(--white);letter-spacing:.5px}
  .band-dot{position:absolute;left:236px;top:200px;width:58px;height:58px;border-radius:50%;background:var(--sky);border:3px solid var(--white)}

  .contact-band{position:absolute;left:262px;top:228px;right:0;height:68px;background:var(--taupe);padding:7px 0 0 34px;list-style:none}
  .contact-band li{display:flex;align-items:center;gap:8px;font-size:12.5px;color:var(--white);line-height:19px}
  .contact-band svg{width:12px;height:12px;flex:none;fill:var(--sky)}

  .abn{position:absolute;left:94px;top:250px;font-size:12px;color:var(--sky);letter-spacing:.4px}
</style>
</head>
<body>
<main class="stage">
  <section class="card card--front" aria-label="Business card front">
    <div class="wordmark">
      <span class="wordmark__name">tbk</span>
      <span class="wordmark__tag">plumbing services</span>
    </div>

    <div class="name-band">
      <p class="name-band__name">Rowan Keddle</p>
      <p class="name-band__title">Director</p>
    </div>
    <span class="band-dot"></span>

    <ul class="contact-band">
      <li><svg viewBox="0 0 24 24" aria-hidden="true"><path d="M6.6 10.8a15.1 15.1 0 0 0 6.6 6.6l2.2-2.2a1 1 0 0 1 1-.25 11.4 11.4 0 0 0 3.6.57 1 1 0 0 1 1 1V20a1 1 0 0 1-1 1A17 17 0 0 1 3 4a1 1 0 0 1 1-1h3.5a1 1 0 0 1 1 1c0 1.25.2 2.45.57 3.57a1 1 0 0 1-.25 1z"/></svg>0431 286 517</li>
      <li><svg viewBox="0 0 24 24" aria-hidden="true"><path d="M12 2a10 10 0 1 0 0 20 10 10 0 0 0 0-20zm6.9 6h-3a15.6 15.6 0 0 0-1.4-3.6A8 8 0 0 1 18.9 8zM12 4a14 14 0 0 1 1.9 4h-3.8A14 14 0 0 1 12 4zM4.3 14a8.2 8.2 0 0 1 0-4h3.4a16.5 16.5 0 0 0 0 4zm.8 2h3a15.6 15.6 0 0 0 1.4 3.6A8 8 0 0 1 5.1 16zm3-8h-3a8 8 0 0 1 4.3-3.6A15.6 15.6 0 0 0 8.1 8zM12 20a14 14 0 0 1-1.9-4h3.8A14 14 0 0 1 12 20zm2.3-6H9.7a14.7 14.7 0 0 1 0-4h4.6a14.7 14.7 0 0 1 0 4zm.3 5.6a15.6 15.6 0 0 0 1.4-3.6h3a8 8 0 0 1-4.4 3.6zm1.7-5.6a16.5 16.5 0 0 0 0-4h3.4a8.2 8.2 0 0 1 0 4z"/></svg>www.tbk-plumbing.com.au</li>
      <li><svg viewBox="0 0 24 24" aria-hidden="true"><path d="M3 5h18a1 1 0 0 1 1 1v12a1 1 0 0 1-1 1H3a1 1 0 0 1-1-1V6a1 1 0 0 1 1-1zm1 2.2V17h16V7.2l-8 5.3z M5 7l7 4.6L19 7z"/></svg>rowan@tbk-plumbing.com.au</li>
    </ul>

    <p class="abn">ABN - 73 215 904 386</p>
  </section>

  <section class="card card--back" aria-label="Business card back">
    <div class="wordmark">
      <span class="wordmark__name">tbk</span>
      <span class="wordmark__tag">plumbing services</span>
    </div>
  </section>
</main>
</body>
</html>
```